KTWG application splash screen

We need a 1024x768 image for use as an application splash screen.
The image will be displayed full screen on an 10 inch industrial PC 1024x768 screen while our application is launching. The image should convey that the application is "Waiting for connection to Wi-Fi access point..." and include a graphic of the industrial PC connected to the access point via an Ethernet cable. A list of troubleshooting steps should be included at the bottom of the image. The troubleshooting steps should not be the main focus of the image and should be shown in a smaller font (but still readable at 1024x768 displayed on a 10 inch screen).
I will include a mock up of the general idea of what we are looking for as well as image files for the industrial PC, a screenshot of our application to show on the PC's screen and the AP.
For general look and feel and a sense of corporate branding please review our website https://marrowgatesoilworks.example/. The splash screen should reflect corporate branding.
Target Market(s)
Users of our application
Industry/Entity Type
Agriculture
Look and feel

```html
<!DOCTYPE html>
<html lang="en">
<head>
<meta charset="utf-8">
<title>KTWG – Waiting for Wi-Fi connection</title>
<link href="https://fonts.googleapis.com/css2?family=Poppins:wght@400;600;700&display=swap" rel="stylesheet">
<style>
  :root {
    --stage: #333333;
    --card-light: #ffffff;
    --card-dark: #cfcfcf;
    --ink: #1f1f1f;
    --body-ink: #3a3a3a;
    --brand-green: #2bb565;
    --device-dark: #2a2a2a;
    --device-mid: #4a4a4a;
    --ap-light: #f4f4f4;
    --ap-shade: #d9d9d9;
  }
  * { margin: 0; padding: 0; box-sizing: border-box; }
  html, body {
    width: 1200px; height: 1200px; overflow: hidden;
    background: var(--stage);
    font-family: "Poppins", sans-serif;
  }
  .splash {
    position: absolute; left: 0; top: 150px;
    width: 1200px; height: 900px;
    background: linear-gradient(135deg, var(--card-light) 0%, #efefef 45%, var(--card-dark) 100%);
    overflow: hidden;
  }
  .wifi-icon { position: absolute; left: 553px; top: 76px; width: 92px; height: 66px; }
  .headline {
    position: absolute; left: 0; top: 140px; width: 1200px;
    text-align: center; color: var(--ink);
    font-weight: 700; font-size: 45px; line-height: 54px; letter-spacing: -0.2px;
  }
  .cab-computer {
    position: absolute; left: 124px; top: 295px; width: 337px; height: 266px;
    border-radius: 16px;
    background: linear-gradient(160deg, var(--device-mid), var(--device-dark));
  }
  .access-point {
    position: absolute; left: 1041px; top: 288px; width: 26px; height: 220px;
    border-radius: 8px;
    background: linear-gradient(90deg, var(--ap-light), var(--ap-shade));
  }
  .cable { position: absolute; left: 0; top: 0; width: 1200px; height: 900px; }
  .label {
    position: absolute; color: var(--ink);
    font-weight: 600; font-size: 18.5px; line-height: 1; white-space: nowrap;
  }
  .label-ap { left: 820px; top: 444px; }
  .label-cable { left: 505px; top: 548px; }
  .label-computer { left: 167px; top: 581px; }
  .troubleshooting { position: absolute; left: 126px; top: 640px; width: 1000px; }
  .troubleshooting-title {
    display: flex; align-items: center; gap: 8px;
    color: var(--brand-green); font-weight: 600; font-size: 20px; line-height: 28px;
  }
  .troubleshooting-title svg { width: 29px; height: 29px; }
  .steps { list-style: none; margin-top: 5px; }
  .steps li {
    position: relative; color: var(--body-ink);
    font-size: 14.6px; line-height: 24.5px; padding-left: 55px;
  }
  .steps li::before {
    content: ""; position: absolute; left: 39px; top: 8px;
    width: 9px; height: 9px; border-radius: 50%; background: var(--ink);
  }
  .steps .sub li { padding-left: 89px; }
  .steps .sub li::before { left: 72px; }
  .steps .sub { list-style: none; }
  .brand-mark {
    position: absolute; left: 983px; top: 796px;
    display: flex; align-items: center; gap: 8px;
    color: var(--ink); font-weight: 700; font-size: 28px; line-height: 1;
  }
  .brand-mark .square { width: 16px; height: 16px; background: var(--brand-green); }
</style>
</head>
<body>
<main class="splash">
  <svg class="wifi-icon" viewBox="0 0 92 66" aria-hidden="true">
    <path d="M4 20 A60 60 0 0 1 88 20" fill="none" stroke="var(--brand-green)" stroke-width="10" stroke-linecap="round"/>
    <path d="M20 36 A38 38 0 0 1 72 36" fill="none" stroke="var(--brand-green)" stroke-width="10" stroke-linecap="round"/>
    <path d="M33 53 L46 66 L59 53 A18 18 0 0 0 33 53 Z" fill="var(--brand-green)"/>
  </svg>

  <h1 class="headline">Waiting for connection to<br>Wi-Fi access point...</h1>

  <svg class="cable" viewBox="0 0 1200 900" aria-hidden="true">
    <rect x="462" y="518" width="14" height="18" rx="3" fill="#1a1a1a"/>
    <path d="M474 527 H1046 Q1054 527 1054 519 V505" fill="none" stroke="#111" stroke-width="4"/>
  </svg>

  <div class="cab-computer" role="img" aria-label="Rugged tractor cab computer showing the seeding application dashboard with green row bar chart"></div>
  <div class="access-point" role="img" aria-label="White outdoor Wi-Fi access point with two antennas and green power light"></div>

  <span class="label label-ap">WI-FI ACCESS POINT</span>
  <span class="label label-cable">ETHERNET CABLE</span>
  <span class="label label-computer">TRACTOR CAB COMPUTER</span>

  <section class="troubleshooting">
    <h2 class="troubleshooting-title">
      <svg viewBox="0 0 29 29" aria-hidden="true">
        <circle cx="14.5" cy="14.5" r="10" fill="none" stroke="var(--brand-green)" stroke-width="2" stroke-dasharray="4 2.5"/>
        <circle cx="14.5" cy="14.5" r="4" fill="none" stroke="var(--brand-green)" stroke-width="2"/>
        <path d="M4 25 L11 18" stroke="var(--brand-green)" stroke-width="2.5" stroke-linecap="round"/>
      </svg>
      Troubleshooting steps:
    </h2>
    <ul class="steps">
      <li>This screen should only be visible for a short time on boot.</li>
      <li>If this screen stays visible for more than a minute:</li>
      <li style="padding-left:0"><ul class="sub">
        <li>Verify that the Wi-Fi Access Point (AP) powers up when this system does (indicated by a green light on the side of the AP).</li>
        <li>Check the Ethernet cable between this system and the AP for damage, and replace it if necessary.</li>
        <li>Power-cycle this system and wait for it to reboot fully.</li>
        <li>If the issue persists, contact KTWG support for further assistance.</li>
      </ul></li>
    </ul>
  </section>

  <div class="brand-mark"><span class="square"></span>KTWG</div>
</main>
</body>
</html>
```